Steadfast Greenwell HEMP Cannabis CBD tinctures

We need packaging for our line of CBD product label design based in Oakland Ca Brand is called 'Steadfast Greenwell'. Our initial product is tincture to help people with pain with out the High effect of THC. I will be attaching og other company sample. The design should communicate slick look and relay health. Use the logo as way to color

Target Market(s)

CBD

Font styles to use
Serif
Decorative

Requirements
Must have
• Design that will make it stand out from the rest of the product on the shelve and be bright.
Nice to have
• The package must be able to stand out and not be dominated by Black color the green color must be the main color.
Should not have
• Be all black and get lost on the shelves

```html
<!DOCTYPE html>
<html lang="en">
<head>
<meta charset="utf-8">
<title>Steadfast Greenwell – CBD Tincture Carton</title>
<link href="https://fonts.googleapis.com/css2?family=Montserrat:wght@400;600;700&family=Oswald:wght@600&display=swap" rel="stylesheet">
<style>
  :root {
    --bg: #eefae4;
    --green: #2fb53f;
    --green-bright: #43c452;
    --green-deep: #138a1f;
    --green-dark: #0f6b18;
    --grey: #8c8c8c;
    --grey-light: #c9c9c9;
    --white: #ffffff;
    --panel: #fafcf9;
  }
  * { margin: 0; padding: 0; box-sizing: border-box; }
  html, body { width: 1200px; height: 1200px; overflow: hidden; }
  body {
    background: var(--bg);
    display: flex; align-items: center; justify-content: center;
    font-family: 'Montserrat', sans-serif;
  }
  .carton { display: flex; width: 600px; height: 1080px; box-shadow: 0 20px 40px rgba(40,90,30,.15); }

  /* side panel */
  .side-panel {
    width: 220px; height: 100%;
    background: linear-gradient(180deg, var(--green-bright), var(--green));
    display: flex; flex-direction: column; align-items: center; justify-content: center; gap: 16px;
    padding: 0 18px;
  }
  .side-panel .mark-square { width: 44px; height: 44px; border: 5px solid var(--white); border-radius: 6px; }
  .side-panel .brand-name { color: var(--white); font-weight: 700; font-size: 22px; text-align: center; line-height: 1.2; }

  /* front panel */
  .front-panel { position: relative; width: 380px; height: 100%; background: var(--panel); overflow: hidden; }
  .pattern-fill { position: absolute; inset: 0; background: linear-gradient(180deg, #f9fcf7, #f2f8ef); }
  .top-band { position: absolute; top: 0; left: 0; right: 0; height: 12px; background: var(--green); }
  .top-rule { position: absolute; top: 12px; left: 0; right: 0; height: 7px; background: var(--grey-light); }
  .format-tab {
    position: absolute; top: 0; left: 50%; transform: translateX(-50%);
    width: 110px; height: 60px; background: var(--green);
    color: var(--white); font-size: 15px; font-weight: 400;
    display: flex; align-items: flex-end; justify-content: center; padding-bottom: 12px;
  }
  .brand-lockup {
    position: absolute; top: 360px; left: 0; right: 0;
    display: flex; flex-direction: column; align-items: center; gap: 22px;
  }
  .brand-lockup .mark-square { width: 90px; height: 90px; border: 10px solid var(--green); border-radius: 12px; }
  .brand-lockup .brand-name { color: var(--green); font-weight: 700; font-size: 27px; }

  .potency-badge { position: absolute; top: 610px; left: 0; right: 0; display: flex; flex-direction: column; align-items: center; }
  .badge-top { width: 210px; height: 100px; position: relative; }
  .badge-top svg { position: absolute; inset: 0; }
  .badge-top .cbd {
    position: absolute; inset: 0; display: flex; align-items: center; justify-content: center; padding-top: 12px;
    font-family: 'Oswald', sans-serif; font-weight: 600; font-size: 62px; color: var(--white); letter-spacing: 1px;
  }
  .extract-row {
    width: 250px; padding: 8px 0; text-align: center;
    border-top: 3px solid #555; border-bottom: 3px solid #555; background: var(--white);
    color: var(--green-deep); font-weight: 600; font-size: 21px; letter-spacing: .5px;
  }
  .extract-foot { width: 190px; height: 12px; background: var(--green-deep); }
  .strength {
    font-family: 'Oswald', sans-serif; font-weight: 600; font-size: 74px; color: var(--green-deep); margin-top: 2px; line-height: 1.15;
  }
  .volume-block {
    position: absolute; left: 85px; width: 210px; top: 880px; bottom: 0;
    background: linear-gradient(90deg, var(--green-bright), var(--green-deep));
    display: flex; align-items: flex-end; justify-content: center; padding-bottom: 32px;
    color: var(--white); font-size: 42px; font-weight: 400;
  }
</style>
</head>
<body>
  <main class="carton">
    <section class="side-panel">
      <span class="mark-square"></span>
      <span class="brand-name">Steadfast Greenwell</span>
    </section>
    <section class="front-panel">
      <div class="pattern-fill" role="img" aria-label="Faint light green geometric cube pattern background"></div>
      <div class="top-band"></div>
      <div class="top-rule"></div>
      <div class="format-tab">TINCTURE</div>

      <div class="brand-lockup">
        <span class="mark-square"></span>
        <span class="brand-name">Steadfast Greenwell</span>
      </div>

      <div class="potency-badge">
        <div class="badge-top">
          <svg viewBox="0 0 210 100" width="210" height="100" aria-hidden="true">
            <polygon points="0,22 105,0 210,22 210,100 0,100" fill="#138a1f"/>
            <polygon points="0,22 105,0 210,22 210,30 105,8 0,30" fill="#0f6b18"/>
          </svg>
          <span class="cbd">CBD</span>
        </div>
        <div class="extract-row">HEMP EXTRACT</div>
        <div class="extract-foot"></div>
        <div class="strength">1500MG</div>
      </div>

      <div class="volume-block">15ml</div>
    </section>
  </main>
</body>
</html>
```